Handyman business card & stationary
Your Home Maintenance Specialist
Handyman business card & stationary - Construction
Creative Brief
Bright & Fun-filled
Dale Kowronski
Owner
4873 Maplecrest Lane Cedarvale, Northland 75214
Dale@steadyfixhomecare.example
steadyfixhomecare.example
Bonded and Insured
Your Home Maintenance Specialist Call of for a free estimate 214-555-0187

```html
<!DOCTYPE html>
<html lang="en">
<head>
<meta charset="utf-8">
<title>SteadyFix Home Care – Business Card</title>
<link rel="stylesheet" href="https://fonts.googleapis.com/css2?family=Montserrat:wght@400;500;600;700;800&display=swap">
<style>
  :root {
    --navy: #2b2a7a;
    --navy-faint: #3d3c8e;
    --red: #d52b3a;
    --white: #ffffff;
    --ink: #3a3a4a;
    --muted: #6c6c7c;
    --backdrop: #c9c9cb;
  }
  * { box-sizing: border-box; margin: 0; padding: 0; }
  html, body { width: 1200px; height: 857px; overflow: hidden; }
  body {
    background: var(--backdrop);
    font-family: "Montserrat", sans-serif;
    position: relative;
  }
  .card {
    position: absolute;
    top: 278px;
    width: 525px;
    height: 300px;
    overflow: hidden;
    border-bottom: 4px solid var(--red);
    border-right: 2px solid var(--red);
  }
  .card--front { left: 48px; background: var(--white); }
  .card--back  { left: 627px; background: var(--navy); }

  .front-band {
    position: absolute; left: 0; top: 0; width: 100%; height: 78px;
    background: var(--navy);
  }
  .front-rule {
    position: absolute; left: 0; top: 78px; width: 100%; height: 3px;
    background: var(--red);
  }
  .holder {
    position: absolute; right: 28px; top: 100px; text-align: right;
  }
  .holder__name { font-size: 17px; font-weight: 700; color: var(--navy); }
  .holder__role { font-size: 10px; font-weight: 500; color: var(--red); letter-spacing: 1px; margin-top: 2px; }
  .holder__address { font-size: 10px; color: var(--muted); margin-top: 8px; line-height: 1.5; }

  .brand { position: absolute; left: 28px; top: 112px; display: flex; align-items: center; gap: 8px; }
  .brand__mark { width: 16px; height: 16px; background: var(--red); }
  .brand__name { font-size: 20px; font-weight: 800; color: var(--navy); letter-spacing: .5px; }
  .brand__tag { position: absolute; left: 28px; top: 142px; font-size: 9px; font-weight: 600; color: var(--red); letter-spacing: 1px; }

  .contacts { position: absolute; left: 28px; bottom: 24px; list-style: none; }
  .contacts li { display: flex; align-items: center; gap: 8px; font-size: 10.5px; color: var(--ink); margin-top: 6px; }
  .contacts svg { width: 14px; height: 14px; flex: none; }

  .back-brand {
    position: absolute; left: 0; right: 0; top: 64px; text-align: center;
    font-size: 30px; font-weight: 800; color: var(--navy-faint); letter-spacing: 1px;
  }
  .back-copy { position: absolute; left: 0; right: 0; top: 148px; color: var(--white); text-align: center; }
  .back-copy__tagline { font-size: 13px; font-weight: 500; opacity: .9; }
  .back-copy__call { font-size: 13px; font-weight: 500; opacity: .9; margin-top: 4px; }
  .back-copy__phone { font-size: 32px; font-weight: 700; margin-top: 8px; letter-spacing: .5px; }
</style>
</head>
<body>
  <section class="card card--front" aria-label="Business card front">
    <div class="front-band"></div>
    <div class="front-rule"></div>

    <div class="brand">
      <span class="brand__mark"></span>
      <span class="brand__name">STEADYFIX</span>
    </div>
    <div class="brand__tag">HOME CARE · BONDED AND INSURED</div>

    <div class="holder">
      <p class="holder__name">Dale Kowronski</p>
      <p class="holder__role">OWNER</p>
      <p class="holder__address">4873 Maplecrest Lane<br>Cedarvale, Northland 75214</p>
    </div>

    <ul class="contacts">
      <li>
        <svg viewBox="0 0 16 16"><circle cx="8" cy="8" r="8" fill="#d52b3a"/><path d="M5.5 4.5l1.5 0 .7 2-1 .8a6 6 0 0 0 2 2l.8-1 2 .7v1.5c0 .5-.5 1-1 1A7 7 0 0 1 4.5 5.5c0-.5.5-1 1-1z" fill="#fff"/></svg>
        214-555-0187
      </li>
      <li>
        <svg viewBox="0 0 16 16"><circle cx="8" cy="8" r="8" fill="#2b2a7a"/><rect x="4" y="5" width="8" height="6" fill="none" stroke="#fff" stroke-width="1"/><path d="M4 5l4 3 4-3" fill="none" stroke="#fff" stroke-width="1"/></svg>
        Dale@steadyfixhomecare.example
      </li>
      <li>
        <svg viewBox="0 0 16 16"><circle cx="8" cy="8" r="8" fill="#2b2a7a"/><circle cx="8" cy="8" r="4" fill="none" stroke="#fff" stroke-width="1"/><path d="M4 8h8M8 4v8" stroke="#fff" stroke-width="1"/></svg>
        steadyfixhomecare.example
      </li>
    </ul>
  </section>

  <section class="card card--back" aria-label="Business card back">
    <div class="back-brand">STEADYFIX</div>
    <div class="back-copy">
      <p class="back-copy__tagline">Your Home Maintenance Specialist</p>
      <p class="back-copy__call">Call of for a free estimate</p>
      <p class="back-copy__phone">214-555-0187</p>
    </div>
  </section>
</body>
</html>
```